Need help in designing new business card utilizing our new logo.

BuildMark Solutions works with Construction Business Owners, Managers & IT Professionals to strengthen software usage and increase user productivity.

Our Construction Accounting and Mobile Field Management Software Clients engage with us in the following areas:

New Software Implementations
Software Re-Implementations
Redesigning Software Usage at the User Level
Project Coordination & Management
Continued Software Support

Old tag line:
Planning Clearly - Delivering Results

www.buildmark-solutions.example

Ridge 4 is a product, but not needed for a new business card.

```html
<!DOCTYPE html>
<html lang="en">
<head>
<meta charset="utf-8">
<title>BuildMark Solutions – Business Card</title>
<link href="https://fonts.googleapis.com/css2?family=Roboto:wght@400;500;700&display=swap" rel="stylesheet">
<style>
  :root {
    --backdrop: #3b3c3e;
    --card: #25262a;
    --blue: #0b4a9e;
    --blue-bright: #1656b8;
    --silver: #c4c6c9;
    --white: #f2f3f5;
    --muted: #b9bbbf;
    --rule: #8c8e92;
  }
  * { box-sizing: border-box; margin: 0; padding: 0; }
  html, body { width: 799px; height: 1200px; overflow: hidden; }
  body {
    background: var(--backdrop);
    font-family: "Roboto", Arial, sans-serif;
    position: relative;
  }
  .card {
    position: absolute;
    left: 80px;
    width: 640px;
    height: 366px;
    background: var(--card);
    border-radius: 22px;
    overflow: hidden;
    box-shadow: 0 14px 30px rgba(0,0,0,.45);
  }
  .card--front { top: 150px; }
  .card--back { top: 690px; }

  /* brand lockup */
  .brand {
    position: absolute;
    display: flex;
    align-items: center;
    gap: 12px;
  }
  .brand__square { width: 30px; height: 30px; }
  .brand__name {
    font-weight: 700;
    font-size: 30px;
    letter-spacing: 1px;
    text-transform: uppercase;
    line-height: 1;
    white-space: nowrap;
  }
  .card--front .brand { top: 62px; left: 0; right: 0; justify-content: center; }
  .card--front .brand__square { background: var(--silver); }
  .card--front .brand__name { color: var(--silver); }
  .card--back .brand { top: 64px; right: 40px; gap: 10px; }
  .card--back .brand__square { width: 26px; height: 26px; background: var(--blue-bright); }
  .card--back .brand__name { color: var(--blue-bright); font-size: 24px; }

  /* front */
  .services {
    position: absolute;
    top: 150px; left: 0; right: 0;
    height: 120px;
    background: var(--blue);
    color: var(--white);
    display: flex;
    flex-direction: column;
    justify-content: center;
    align-items: center;
    font-size: 17px;
    line-height: 1.5;
    text-align: center;
  }
  .services__sep { margin: 0 10px; }
  .front-web {
    position: absolute;
    top: 300px; left: 0; right: 0;
    display: flex;
    align-items: center;
    justify-content: center;
    gap: 22px;
    color: var(--white);
    font-size: 16px;
  }
  .front-web__dash { width: 50px; height: 2px; background: var(--muted); }

  /* back */
  .holder {
    position: absolute;
    top: 52px; left: 34px;
  }
  .holder__name { color: var(--blue-bright); font-size: 22px; font-weight: 700; white-space: nowrap; }
  .holder__role { color: var(--white); font-size: 14px; margin-top: 4px; }
  .holder-accent {
    position: absolute;
    left: -8px; top: 54px;
    width: 16px; height: 34px;
    border-radius: 0 17px 17px 0;
    background: var(--blue-bright);
  }
  .divider {
    position: absolute;
    top: 112px; left: 90px; right: 40px;
    height: 1px; background: var(--rule);
  }
  .contacts {
    position: absolute;
    top: 136px; left: 34px;
    list-style: none;
    color: var(--white);
    font-size: 15px;
    line-height: 1;
  }
  .contacts li { display: flex; align-items: center; gap: 12px; margin-bottom: 11px; }
  .contacts svg { width: 13px; height: 13px; fill: var(--blue-bright); flex: none; }
  .address {
    position: absolute;
    top: 250px; right: 40px;
    text-align: left;
    color: var(--white);
    font-size: 15.5px;
    line-height: 1.45;
  }
  .address-rule {
    position: absolute;
    top: 302px; right: 40px;
    width: 250px; height: 1px; background: var(--rule);
  }
  .base-stripe {
    position: absolute;
    left: 0; bottom: 0;
    width: 260px; height: 18px;
    background: var(--silver);
  }
  .tagline-band {
    position: absolute;
    right: 0; bottom: 0;
    width: 390px; height: 40px;
    background: var(--blue);
    border-top-left-radius: 28px;
    display: flex;
    align-items: center;
    justify-content: flex-end;
    padding-right: 40px;
    color: var(--white);
    font-size: 16px;
    white-space: nowrap;
  }
</style>
</head>
<body>

  <section class="card card--front">
    <div class="brand">
      <span class="brand__square"></span>
      <span class="brand__name">BuildMark Solutions</span>
    </div>
    <div class="services">
      <p>New Software Implementations<span class="services__sep">|</span>Software Re-Implementations</p>
      <p>Redesigning Software Usage at the User Level</p>
      <p>Project Coordination &amp; Management<span class="services__sep">|</span>Continued Software Support</p>
    </div>
    <div class="front-web">
      <span class="front-web__dash"></span>
      <span>www.buildmark-solutions.example</span>
      <span class="front-web__dash"></span>
    </div>
  </section>

  <section class="card card--back">
    <span class="holder-accent"></span>
    <div class="holder">
      <p class="holder__name">Dana R. Whitfield</p>
      <p class="holder__role">Owner</p>
    </div>
    <div class="brand">
      <span class="brand__square"></span>
      <span class="brand__name">BuildMark Solutions</span>
    </div>
    <div class="divider"></div>
    <ul class="contacts">
      <li>
        <svg viewBox="0 0 16 16" aria-hidden="true"><rect x="4" y="1" width="8" height="14" rx="1.5"/><rect x="5.5" y="3" width="5" height="8" fill="#25262a"/></svg>
        <span>555-010-4821</span>
      </li>
      <li>
        <svg viewBox="0 0 16 16" aria-hidden="true"><path d="M3 1h3l1.5 4-2 1.3a9 9 0 0 0 4.2 4.2L11 8.5l4 1.5v3a2 2 0 0 1-2 2C6.4 15 1 9.6 1 3a2 2 0 0 1 2-2z"/></svg>
        <span>555-010-7300 ext. 100</span>
      </li>
      <li>
        <svg viewBox="0 0 16 16" aria-hidden="true"><path d="M1 3h14v10H1z"/><path d="M1 3l7 6 7-6" fill="none" stroke="#25262a" stroke-width="1.4"/></svg>
        <span>dana.whitfield@buildmark-solutions.example</span>
      </li>
      <li>
        <svg viewBox="0 0 16 16" aria-hidden="true"><circle cx="8" cy="8" r="7"/><path d="M1 8h14M8 1c-3 3.5-3 10.5 0 14M8 1c3 3.5 3 10.5 0 14" fill="none" stroke="#25262a" stroke-width="1.1"/></svg>
        <span>www.buildmark-solutions.example</span>
      </li>
    </ul>
    <div class="address">
      <p>14B Alder Street - PMB 118</p>
      <p>Millbrook Falls, NY 10999</p>
    </div>
    <div class="address-rule"></div>
    <div class="base-stripe"></div>
    <div class="tagline-band">Planning Clearly - Delivering Results</div>
  </section>

</body>
</html>
```